Redesign of business card for Cedar Ridge Mechanical

We are looking for a new design for our business cards for Cedar Ridge Mechanical. We are a plumbing & HVAC construction company, operating on the West Coast of Canada and USA. Logo attached.
Industry/Entity Type
Construction - Plumbing & HVAC
Contact Information for Business Card
Name, address, phone numbers, email, website address
Look and feel
Each slider illustrates characteristics of the customer's brand and the style your logo design should communicate.

```html
<!DOCTYPE html>
<html lang="en">
<head>
<meta charset="utf-8">
<title>Cedar Ridge Mechanical – Business Card</title>
<link rel="stylesheet" href="https://fonts.googleapis.com/css2?family=Montserrat:wght@400;500;700&display=swap">
<style>
  :root {
    --stage: #2b2b2b;
    --paper: #ffffff;
    --ink: #1c1c1c;
    --muted: #8a8a8a;
    --rule: #9a9a9a;
    --band: #1f1f1f;
  }
  * { box-sizing: border-box; margin: 0; padding: 0; }
  html, body { width: 1200px; height: 801px; overflow: hidden; }
  body {
    background: var(--stage);
    font-family: "Montserrat", sans-serif;
    color: var(--ink);
    display: flex;
    align-items: center;
    justify-content: center;
    gap: 40px;
  }
  .card {
    position: relative;
    width: 540px;
    height: 309px;
    background: var(--paper);
    border-radius: 22px;
    overflow: hidden;
  }
  /* Front: contact side */
  .brand {
    position: absolute;
    top: 44px;
    right: 40px;
    display: flex;
    align-items: center;
    gap: 10px;
    font-size: 15px;
    font-weight: 700;
    letter-spacing: 1.5px;
    text-transform: uppercase;
    color: var(--ink);
  }
  .brand-mark { width: 14px; height: 14px; background: var(--ink); }
  .divider {
    position: absolute;
    left: 36px;
    right: 36px;
    top: 112px;
    height: 1px;
    background: var(--rule);
  }
  .address {
    position: absolute;
    right: 40px;
    top: 128px;
    text-align: right;
    font-size: 13px;
    line-height: 1.45;
    color: var(--muted);
  }
  .person { position: absolute; left: 36px; top: 140px; }
  .person-name { font-size: 19px; font-weight: 700; letter-spacing: 1px; text-transform: uppercase; }
  .person-name .surname { color: var(--muted); }
  .person-role { font-size: 13px; margin-top: 2px; }
  .person-rule { width: 250px; height: 1px; background: var(--rule); margin: 10px 0; }
  .contact { list-style: none; font-size: 14px; line-height: 1.6; }
  .contact li { display: flex; align-items: center; gap: 8px; }
  .contact svg { width: 13px; height: 13px; fill: var(--ink); }
  .band {
    position: absolute;
    left: 0; right: 0; bottom: 0;
    height: 34px;
    background: var(--band);
    clip-path: polygon(48% 0, 100% 0, 100% 100%, 44% 100%);
  }
  .website {
    position: absolute;
    right: 36px;
    bottom: 9px;
    font-size: 13px;
    color: var(--paper);
    letter-spacing: 0.5px;
  }
  /* Back: brand side */
  .card-back { display: flex; align-items: center; justify-content: center; }
  .back-brand {
    display: flex;
    align-items: center;
    gap: 14px;
    font-size: 26px;
    font-weight: 700;
    letter-spacing: 2px;
    text-transform: uppercase;
    color: var(--ink);
  }
  .back-brand .brand-mark { width: 22px; height: 22px; }
</style>
</head>
<body>
  <article class="card card-front">
    <div class="brand"><span class="brand-mark"></span>Cedar Ridge Mechanical</div>
    <div class="divider"></div>
    <p class="address">Your address, city<br>state, ZIP 0000</p>
    <div class="person">
      <h1 class="person-name">Daniel <span class="surname">Reyes</span></h1>
      <p class="person-role">Manager</p>
      <div class="person-rule"></div>
      <ul class="contact">
        <li><svg viewBox="0 0 24 24" aria-hidden="true"><path d="M6.6 10.8a15.1 15.1 0 0 0 6.6 6.6l2.2-2.2c.3-.3.7-.4 1-.2 1.1.4 2.3.6 3.6.6.6 0 1 .4 1 1V20c0 .6-.4 1-1 1A17 17 0 0 1 3 4c0-.6.4-1 1-1h3.5c.6 0 1 .4 1 1 0 1.3.2 2.5.6 3.6.1.3 0 .7-.2 1z"/></svg>604-555-0187</li>
        <li><svg viewBox="0 0 24 24" aria-hidden="true"><path d="M2 5h20v14H2zm2 2v.5l8 5 8-5V7l-8 5z"/></svg>daniel@cedarridgemech.com</li>
      </ul>
    </div>
    <div class="band"></div>
    <p class="website">www.cedarridgemech.com</p>
  </article>

  <article class="card card-back">
    <div class="back-brand"><span class="brand-mark"></span>Cedar Ridge Mechanical</div>
  </article>
</body>
</html>
```